The logo name is "Harbor Skin". The name of the product will be "Cutaneous Comfort". This product is specifically formulated for amputees. Therefore under the product name it should state "for amputees". The catch phrase will be "Experience Harbor find Calmness"
These are the things we need on the label:
Logo, product name, "for amputees", "Experience Harbor find Calmness", Safe, Effective, Directions: spray on problem areas, no need to dry off. harborskin.example, Made in Canada, 500ml.
The MOST IMPORTANT and therefore the most prominent thing on this lable will be the LOGO! The second most prominent thing will be the word "Comfort" We want to keep it very plain, very simple, very unclutered. Keep in mind that this lable will be placed on a white bottle or have a white back ground. The 500ml white PE bottle with trigger sprayer will have a tear drop label. See attached die line (S-294).
We want to stay with the colours that goes with the colour scheme of the logo. See attached logo. Soft colours. We do not want a picture! We would like the lable to be classy and rich.
Updates
The logo name is "Harbor Skin". The name of the product will be "Cutaneous Comfort". This product is specificlly formulated for amputees. Therefore under the product name it should state "for amputees". The catch phrase will be "Experience Harbor find Calmness"
Logo, product name, "for amputees", catch phrase "Experience Harbor find Calmness", Clean, Safe, Effective, Directions: spray on problem areas, no need to dry off. Also Harbor Skin Corpation, harborskin.example, Made in Canada, 500ml.
We want to stay with the colour scheme of the logo. See attached logo. Soft colours. We do not want a picture! We would like the lable to be classy and rich.
This is the offical directive that came from the governing panal of this lable. This panal it not know where it wanted to take this lable that would represent this line until they review all of your submissions, thank you for all your talented hard work. But now it is clear it is time to regroup and hit this objective.
Project Deadline Extended
Reason: New restrictions on lable wording for this product.
Target Market(s)
Amputees and Parents of.
Industry/Entity Type
Product
Requirements
Must have
- Final product to be in a pdf or an illustrator file

```html
<!DOCTYPE html>
<html lang="en">
<head>
<meta charset="utf-8">
<title>Harbor Skin – Cutaneous Comfort Label</title>
<link rel="stylesheet" href="https://fonts.googleapis.com/css2?family=Fjalla+One&family=Libre+Baskerville&family=Parisienne&family=Arimo&display=swap">
<style>
  :root {
    --backdrop-top: #eef2ef;
    --backdrop-bottom: #c9d6cd;
    --label-white: #ffffff;
    --brand-green: #1f6b4a;
    --brand-teal: #5fb5ad;
    --band-red: #b3202a;
    --band-grey: #bfc5c2;
    --field-dark: #0f4a32;
    --field-mid: #23734f;
    --glow: #a9e07a;
    --tagline: #e2d48c;
    --bullet: #f09a2a;
    --small-text: #ffffff;
  }
  html, body {
    margin: 0;
    width: 823px;
    height: 1200px;
    overflow: hidden;
  }
  body {
    background: linear-gradient(180deg, var(--backdrop-top), var(--backdrop-bottom));
  }
  .label-art {
    display: block;
    width: 823px;
    height: 1200px;
  }
  .brand-name {
    font-family: "Libre Baskerville", Georgia, serif;
    fill: var(--brand-green);
    font-size: 66px;
  }
  .product-name {
    font-family: "Fjalla One", "Arial Narrow", sans-serif;
    fill: var(--label-white);
    font-size: 52px;
  }
  .product-audience {
    font-size: 32px;
  }
  .product-claim {
    font-family: "Fjalla One", "Arial Narrow", sans-serif;
    fill: var(--brand-green);
    font-size: 34px;
    letter-spacing: 0.5px;
  }
  .tagline {
    font-family: "Parisienne", cursive;
    fill: var(--tagline);
    font-size: 34px;
  }
  .info-line {
    font-family: "Arimo", Arial, sans-serif;
    fill: var(--small-text);
    font-size: 19px;
  }
  .info-bullet { fill: var(--bullet); }
</style>
</head>
<body>
<svg class="label-art" viewBox="0 0 823 1200" xmlns="http://www.w3.org/2000/svg">
  <defs>
    <clipPath id="label-shape">
      <rect x="101" y="100" width="620" height="1000" rx="14"/>
    </clipPath>
    <linearGradient id="field-fill" x1="0" y1="0" x2="0" y2="1">
      <stop offset="0" stop-color="var(--field-mid)"/>
      <stop offset="1" stop-color="var(--field-dark)"/>
    </linearGradient>
    <linearGradient id="claim-fill" x1="0" y1="0" x2="1" y2="0">
      <stop offset="0" stop-color="#ffffff" stop-opacity="0"/>
      <stop offset="0.45" stop-color="#ffffff"/>
      <stop offset="1" stop-color="var(--band-grey)"/>
    </linearGradient>
    <radialGradient id="glow-fill" cx="0.45" cy="0.45" r="0.6">
      <stop offset="0" stop-color="var(--glow)" stop-opacity="0.75"/>
      <stop offset="0.5" stop-color="var(--glow)" stop-opacity="0.22"/>
      <stop offset="1" stop-color="var(--glow)" stop-opacity="0"/>
    </radialGradient>
  </defs>

  <g class="label" clip-path="url(#label-shape)">
    <rect class="label-base" x="101" y="100" width="620" height="1000" fill="var(--label-white)"/>

    <g class="brand-block">
      <rect class="brand-mark" x="131" y="170" width="84" height="84" fill="var(--brand-teal)"/>
      <text class="brand-name" x="236" y="240">Harbor Skin</text>
    </g>

    <polygon class="colour-field" points="101,505 721,370 721,1100 101,1100" fill="url(#field-fill)"/>

    <polygon class="claim-strip" points="101,505 721,370 721,430 101,565" fill="url(#claim-fill)"/>
    <text class="product-claim" x="0" y="0" text-anchor="end"
          transform="translate(704 420) rotate(-12.3)">Naturally Hygienic</text>

    <polygon class="name-band" points="101,430 721,295 721,370 101,505" fill="var(--band-red)"/>
    <text class="product-name" transform="translate(118 486) rotate(-12.3)" textLength="580" lengthAdjust="spacingAndGlyphs">Cutaneous Comfort <tspan class="product-audience">for amputees</tspan></text>

    <rect class="glow-visual" role="img" aria-label="Glowing green strand of light sweeping across the field"
          x="131" y="560" width="520" height="230" fill="url(#glow-fill)"/>

    <text class="tagline" x="140" y="875">Experience Harbor find Calmness</text>

    <g class="info-list">
      <circle class="info-bullet" cx="150" cy="918" r="5"/>
      <text class="info-line" x="166" y="925">Directions: spray on problem areas, no need to dry off.</text>
      <circle class="info-bullet" cx="150" cy="950" r="5"/>
      <text class="info-line" x="166" y="957">Clean · Safe · Effective · Made in Canada · 500ml</text>
      <circle class="info-bullet" cx="150" cy="982" r="5"/>
      <text class="info-line" x="166" y="989">Harbor Skin Corpation · harborskin.example</text>
    </g>
  </g>
</svg>
</body>
</html>
```